Wellpath Ledgers New Website

Please review the attached Design Brief with additional details. Thank you!

The goal is to create a website that effectively communicates the benefits of WellPath Ledgers to eye care professionals. The website should streamline the process of understanding and utilizing WellPath Ledgers' services, emphasizing improved patient outcomes, increased referrals, and enhanced patient engagement.

Target Market(s)

Eyecare Professionals

Number of Pages Required

4 page

```html
<!DOCTYPE html>
<html lang="en">
<head>
<meta charset="utf-8">
<title>Wellpath Ledgers – Services</title>
<link href="https://fonts.googleapis.com/css2?family=Open+Sans:wght@400;600;700&family=Mulish:wght@400;600;700&display=swap" rel="stylesheet">
<style>
:root{
  --navy:#1a3f6e;
  --navy-deep:#0f4a75;
  --ink:#3a3a3a;
  --body:#5a5a5a;
  --orange:#f6a33a;
  --cyan:#2cb5e6;
  --soft:#f3f8fc;
  --icon-bg:#e8eff6;
  --topbar:#1d3a68;
  --footer:#1c1530;
  --footer-text:#c9c6d6;
  --accent-green:#3f7d6d;
}
*{box-sizing:border-box;margin:0;padding:0}
html,body{width:1200px;height:2930px;overflow:hidden}
body{position:relative;font-family:"Mulish",sans-serif;color:var(--body);background:#fff}
.abs{position:absolute}

/* header */
.topbar{left:0;top:0;width:1200px;height:46px;background:var(--topbar)}
.topbar-info{top:16px;font-size:10.5px;color:#fff;display:flex;align-items:center;gap:6px}
.pin{width:9px;height:11px}
.social-dot{display:inline-block;width:8px;height:8px;background:#fff;border-radius:2px;margin-left:5px}
.quote-btn{left:845px;top:20px;width:112px;height:15px;background:var(--accent-green);color:#fff;font-size:10px;text-align:center;line-height:15px;letter-spacing:.3px}
.navbar{left:0;top:46px;width:1200px;height:45px;background:#fff}
.brand-panel{left:0;top:0;width:440px;height:91px}
.brand{left:78px;top:30px;display:flex;align-items:center;gap:8px}
.brand-mark{width:22px;height:22px;border-radius:50%;background:var(--orange)}
.brand-name{font-family:"Open Sans",sans-serif;font-weight:600;font-size:22px;color:#1d4fb0}
.brand-tag{left:82px;top:70px;font-size:12px;color:#222}
.nav{top:62px;font-size:12px;color:#777}
.nav.active{color:#2c6db3}
.nav.current{color:var(--navy-deep);font-weight:700}

/* hero */
.hero{left:0;top:91px;width:1200px;height:256px;background:linear-gradient(100deg,#2a4f7e 0%,#3c6a98 45%,#4d7aa8 70%,#2f5680 100%)}
.hero-rule{left:0;top:347px;width:1200px;height:4px;background:var(--orange)}
.hero-kicker{left:107px;top:187px;color:#fff;font-size:20px;font-family:"Open Sans",sans-serif}
.hero-title{left:106px;top:216px;color:#fff;font-size:50px;font-weight:700;font-family:"Open Sans",sans-serif}

/* services */
.band{left:0;width:1200px;overflow:hidden}
.band.soft{background:var(--soft)}
.svc-title{font-family:"Open Sans",sans-serif;font-size:34px;font-weight:600;color:var(--ink);letter-spacing:.5px}
.svc-title b{color:var(--navy-deep);font-weight:700}
.dash{width:36px;height:2px;background:var(--orange)}
.svc-text{width:412px;font-size:13.5px;line-height:25px;color:var(--body)}
.btn-outline{width:116px;height:31px;border:2px solid var(--navy-deep);border-radius:16px;font-size:10.5px;font-weight:700;color:var(--navy-deep);text-align:center;line-height:27px;letter-spacing:.5px}
.photo-disc{border-radius:50%;border:4px solid transparent;border-left-color:#2867b0;border-top-color:#2867b0}
.icon-disc{width:116px;height:116px;border-radius:50%;background:var(--icon-bg);display:flex;align-items:center;justify-content:center}

/* registries */
.reg-kicker{left:0;width:1212px;top:1701px;text-align:center;font-size:14px;color:var(--cyan);text-decoration:underline;text-underline-offset:4px}
.reg-title{left:0;width:1212px;top:1738px;text-align:center;font-family:"Open Sans",sans-serif;font-size:43px;font-weight:700;color:var(--navy)}
.reg-card{width:327px;height:210px;overflow:hidden}
.reg-card .tab{left:0;top:0;width:8px;height:51px;background:var(--orange)}
.reg-card .shade{left:0;bottom:0;width:100%;height:80px;background:linear-gradient(transparent,rgba(0,0,0,.55))}
.reg-card .label{right:60px;bottom:22px;color:#fff;font-family:"Open Sans",sans-serif;font-weight:700;font-size:16px;letter-spacing:.3px}
.reg-card .badge{right:0;bottom:7px;width:52px;height:52px;background:var(--cyan);display:flex;align-items:center;justify-content:center}
.upcoming{left:793px;top:1831px;width:324px;height:457px;background:#fff;border:2px solid #e6ebf1;padding:26px 24px}
.upcoming h3{font-family:"Open Sans",sans-serif;font-weight:600;font-size:18.5px;color:var(--navy);margin-bottom:8px}
.upcoming p{font-size:12.5px;line-height:25px;color:var(--body)}

/* footer */
.footer-bg{left:0;top:2360px;width:1200px;height:570px}
.foot-brand{left:117px;top:2500px;display:flex;align-items:center;gap:10px}
.foot-brand .brand-name{font-size:30px;color:#2157c8;font-weight:400}
.foot-text{font-size:13px;line-height:21px;color:var(--footer-text)}
.soc{top:2661px;width:32px;height:32px;border-radius:4px;background:#2e2848}
.soc.on{background:var(--orange)}
.soc i{display:block;width:8px;height:8px;margin:12px;border-radius:2px;background:#8e88a8}
.soc.on i{background:#fff}
.foot-head{font-family:"Open Sans",sans-serif;font-weight:700;font-size:15px;color:#fff}
.foot-link{font-size:12.5px;color:var(--footer-text)}
.news-input{left:827px;top:2605px;width:193px;height:47px;background:#fff;font-size:12px;color:#777;padding-left:24px;line-height:47px}
.news-btn{left:1020px;top:2605px;width:49px;height:47px;background:var(--orange);display:flex;align-items:center;justify-content:center}
.ci{top:2758px;width:50px;height:50px;border-radius:50%;background:#2e2848;display:flex;align-items:center;justify-content:center}
.ci.on{background:var(--orange)}
.ct h4{font-family:"Open Sans",sans-serif;font-weight:700;font-size:16px;color:#fff}
.ct p{font-size:12.5px;color:var(--footer-text);margin-top:4px}
.foot-rule{left:125px;top:2874px;width:948px;height:1px;background:#3a3356}
.copyright{left:0;width:1190px;top:2895px;text-align:center;font-size:13px;color:#fff;letter-spacing:.3px}
</style>
</head>
<body>

<!-- header -->
<div class="abs topbar"></div>
<div class="abs topbar-info" style="left:468px">
  <svg class="pin" viewBox="0 0 9 11"><path d="M4.5 0a4 4 0 0 0-4 4c0 3 4 7 4 7s4-4 4-7a4 4 0 0 0-4-4z" fill="#fff"/><circle cx="4.5" cy="4" r="1.5" fill="#1d3a68"/></svg>
  48 Linden Row, Fairmont, 204117
</div>
<div class="abs topbar-info" style="left:706px">Follow Us: <span class="social-dot"></span><span class="social-dot"></span><span class="social-dot"></span></div>
<div class="abs quote-btn">GET QUOTATION</div>
<div class="abs navbar"></div>
<svg class="abs brand-panel" viewBox="0 0 440 91"><path d="M0 23H395C415 23 420 46 440 46V91H0Z" fill="#fff"/></svg>
<div class="abs brand"><span class="brand-mark"></span><span class="brand-name">Wellpath Ledgers</span></div>
<div class="abs brand-tag">Empowering Healthcare</div>
<div class="abs nav active" style="left:449px">Home</div>
<div class="abs nav" style="left:543px">About Us</div>
<div class="abs nav" style="left:630px">Conditions</div>
<div class="abs nav current" style="left:724px">Services</div>
<div class="abs nav" style="left:830px">Gallery</div>
<div class="abs nav" style="left:911px">Team</div>
<div class="abs nav" style="left:993px">Contact Us</div>

<!-- hero -->
<div class="abs hero" role="img" aria-label="Medical researchers working at computers in a lab, blue tint"></div>
<div class="abs hero-rule"></div>
<div class="abs hero-kicker">OUR SERVICES</div>
<div class="abs hero-title">Services We Offer</div>

<!-- service 1 -->
<section class="abs band" style="top:351px;height:422px">
  <div class="abs photo-disc" style="left:747px;top:65px;width:560px;height:560px;transform:rotate(-20deg);background:linear-gradient(135deg,#cfd8e0,#8fa8bf 55%,#5c86b0)" role="img" aria-label="Clinician in mask and gown working at a computer"></div>
  <div class="abs icon-disc" style="left:721px;top:106px">
    <svg width="52" height="52" viewBox="0 0 52 52" fill="none" stroke="#f6a33a" stroke-width="2.5"><circle cx="24" cy="24" r="18"/><path d="M8 18c8 2 10 8 18 6M14 36c2-6 8-6 10-12"/><circle cx="37" cy="37" r="6" fill="#e8eff6"/><circle cx="37" cy="37" r="2"/></svg>
  </div>
  <h2 class="abs svc-title" style="left:147px;top:80px">Health <b>Analytics</b></h2>
  <div class="abs dash" style="left:146px;top:154px"></div>
  <p class="abs svc-text" style="left:194px;top:141px">Lorem ipsum dolor sit amet, consectetur adipiscing elit, sed do eiusmod tempor incididunt ut labore et dolore magna aliqua. Ut enim ad minim veniam, quis nostrud exercitation ullamco laboris nisi ut aliquip ex ea commodo consequat. Duis aute irure dolor in reprehenderit in voluptate velit esse cillum dolore eu fugiat nulla paria</p>
  <div class="abs btn-outline" style="left:194px;top:300px">CONTACT US</div>
</section>

<!-- service 2 -->
<section class="abs band soft" style="top:773px;height:421px">
  <div class="abs photo-disc" style="left:-111px;top:65px;width:564px;height:564px;transform:rotate(100deg);background:linear-gradient(135deg,#e8e3d8,#c9bca6 55%,#8f8670)" role="img" aria-label="Doctor in white coat writing notes at a desk"></div>
  <div class="abs icon-disc" style="left:363px;top:102px">
    <svg width="44" height="44" viewBox="0 0 44 44" fill="none" stroke="#f6a33a" stroke-width="2.5"><path d="M22 4l4 5 6-1 1 6 5 4-3 5 3 5-5 4-1 6-6-1-4 5-4-5-6 1-1-6-5-4 3-5-3-5 5-4 1-6 6 1z"/><circle cx="22" cy="22" r="7"/></svg>
  </div>
  <h2 class="abs svc-title" style="left:602px;top:80px">Outcome <b>Monitoring</b></h2>
  <div class="abs dash" style="left:601px;top:160px"></div>
  <p class="abs svc-text" style="left:649px;top:147px">Lorem ipsum dolor sit amet, consectetur adipiscing elit, sed do eiusmod tempor incididunt ut labore et dolore magna aliqua. Ut enim ad minim veniam, quis nostrud exercitation ullamco laboris nisi ut aliquip ex ea commodo consequat. Duis aute irure dolor in reprehenderit in voluptate velit esse cillum dolore eu fugiat nulla paria</p>
  <div class="abs btn-outline" style="left:649px;top:305px">CONTACT US</div>
</section>

<!-- service 3 -->
<section class="abs band" style="top:1194px;height:446px">
  <div class="abs photo-disc" style="left:747px;top:63px;width:560px;height:560px;transform:rotate(-20deg);background:linear-gradient(135deg,#7d94ad,#b9c6d3 50%,#4d6680)" role="img" aria-label="Stethoscope on a desk beside hands typing on a laptop"></div>
  <div class="abs icon-disc" style="left:721px;top:103px">
    <svg width="46" height="46" viewBox="0 0 46 46" fill="none" stroke="#f6a33a" stroke-width="2.5"><circle cx="23" cy="13" r="6"/><circle cx="10" cy="17" r="4"/><circle cx="36" cy="17" r="4"/><path d="M12 40v-6a11 11 0 0 1 22 0v6zM3 34a7 7 0 0 1 9-6M43 34a7 7 0 0 0-9-6"/></svg>
  </div>
  <h2 class="abs svc-title" style="left:147px;top:80px">Engagement <b>Tools</b></h2>
  <div class="abs dash" style="left:146px;top:151px"></div>
  <p class="abs svc-text" style="left:194px;top:138px">Lorem ipsum dolor sit amet, consectetur adipiscing elit, sed do eiusmod tempor incididunt ut labore et dolore magna aliqua. Ut enim ad minim veniam, quis nostrud exercitation ullamco laboris nisi ut aliquip ex ea commodo consequat. Duis aute irure dolor in reprehenderit in voluptate velit esse cillum dolore eu fugiat nulla paria</p>
  <div class="abs btn-outline" style="left:194px;top:296px">CONTACT US</div>
</section>

<!-- registries -->
<section class="abs band soft" style="top:1640px;height:760px"></section>
<div class="abs reg-kicker">OUR REGISTRIES</div>
<h2 class="abs reg-title">Our Most Popular Registries</h2>

<div class="abs reg-card" style="left:85px;top:1831px;background:linear-gradient(135deg,#f1eeea,#d9d2c8 60%,#b7ab9c)" role="img" aria-label="Woman resting on a sofa at home">
  <div class="abs shade"></div><div class="abs tab"></div>
  <div class="abs label">Diabetes Management Registry</div>
  <div class="abs badge"><svg width="32" height="32" viewBox="0 0 32 32" fill="none" stroke="#fff" stroke-width="2"><circle cx="15" cy="15" r="11"/><path d="M5 11c5 1 7 5 11 4M9 23c1-4 5-4 6-8"/><circle cx="23" cy="23" r="4" fill="#2cb5e6"/></svg></div>
</div>
<div class="abs reg-card" style="left:439px;top:1831px;background:linear-gradient(135deg,#eef0f2,#c8ced4 55%,#7f8a96)" role="img" aria-label="Doctor holding a tablet">
  <div class="abs shade"></div><div class="abs tab"></div>
  <div class="abs label">Cataract Extraction Registry</div>
  <div class="abs badge"><svg width="32" height="32" viewBox="0 0 32 32" fill="none" stroke="#fff" stroke-width="2"><circle cx="15" cy="15" r="11"/><path d="M5 11c5 1 7 5 11 4M9 23c1-4 5-4 6-8"/><circle cx="23" cy="23" r="4" fill="#2cb5e6"/></svg></div>
</div>
<div class="abs reg-card" style="left:85px;top:2074px;background:linear-gradient(135deg,#5a6670,#c9d0d6 45%,#e9ecef)" role="img" aria-label="Woman reviewing data on computer monitors">
  <div class="abs shade"></div><div class="abs tab"></div>
  <div class="abs label">Dry Eye Registry</div>
  <div class="abs badge"><svg width="32" height="32" viewBox="0 0 32 32" fill="none" stroke="#fff" stroke-width="2"><circle cx="15" cy="15" r="11"/><path d="M5 11c5 1 7 5 11 4M9 23c1-4 5-4 6-8"/><circle cx="23" cy="23" r="4" fill="#2cb5e6"/></svg></div>
</div>
<div class="abs reg-card" style="left:439px;top:2074px;background:linear-gradient(135deg,#8ea2b8,#c3ccd6 50%,#3f5169)" role="img" aria-label="Stethoscope beside a calculator and laptop">
  <div class="abs shade"></div><div class="abs tab"></div>
  <div class="abs label">Myopia Registry</div>
  <div class="abs badge"><svg width="32" height="32" viewBox="0 0 32 32" fill="none" stroke="#fff" stroke-width="2"><circle cx="15" cy="15" r="11"/><path d="M5 11c5 1 7 5 11 4M9 23c1-4 5-4 6-8"/><circle cx="23" cy="23" r="4" fill="#2cb5e6"/></svg></div>
</div>

<aside class="abs upcoming">
  <h3>Our Upcoming Registries</h3>
  <p>Lorem ipsum dolor sit amet, consectetur adipiscing elit, sed do eiusmod tempor incididunt ut labore et dolore magna aliqua. Ut enim ad minim veniam, quis nostrud exercitation ullamco laboris nisi ut aliquip ex ea commodo consequat. Duis aute irure dolor in reprehenderit in volu ptate velit esse cillum dolore eu fugiat nulla paria</p>
  <p>Lorem ipsum dolor sit amet, consectetur adipiscing elit, sed do eiusmod tempor incididunt ut labore et dolore magna aliqua. Ut enim ad minim veniam, quis nostrud exercitation ullamco laboris nisi ut aliquip ex ea commodo consequat. Duis aute irure dolor in reprehenderit in volu ptate velit esse cillum dolore</p>
</aside>

<!-- footer -->
<svg class="abs footer-bg" viewBox="0 0 1200 570" preserveAspectRatio="none">
  <path d="M0 80C120 40 250 15 420 15C650 15 850 70 1200 75V570H0Z" fill="#f6a33a"/>
  <path d="M0 85C200 75 320 40 520 60C700 78 900 95 1200 80V570H0Z" fill="#1c1530"/>
</svg>

<div class="abs foot-brand"><span class="brand-mark" style="width:30px;height:30px"></span><span class="brand-name">Wellpath Ledgers</span></div>
<p class="abs foot-text" style="left:125px;top:2574px;width:300px">Lorem ipsum dolor sit amet, consectetur adipiscing elit, sed do eiusmod tempor incididunt ut</p>
<div class="abs soc on" style="left:125px"><i></i></div>
<div class="abs soc" style="left:163px"><i></i></div>
<div class="abs soc" style="left:201px"><i></i></div>
<div class="abs soc" style="left:239px"><i></i></div>

<div class="abs foot-head" style="left:489px;top:2505px">Quick Links</div>
<div class="abs foot-link" style="left:490px;top:2551px;line-height:25.8px">Home<br>Services<br>About Us<br>Contact<br>Blog<br>Testimonials</div>
<div class="abs foot-link" style="left:625px;top:2551px;line-height:25.8px">Cookies Policy<br>Terms of Use<br>Careers<br>Our Team<br>More</div>

<div class="abs foot-head" style="left:827px;top:2505px">Newsletters</div>
<p class="abs foot-text" style="left:827px;top:2546px;width:250px;font-size:12.5px">Lorem ipsum dolor sit amet, consectetur adipiscing elit, sed do eiusmod tempor</p>
<div class="abs news-input">Enter Email Address</div>
<div class="abs news-btn"><svg width="14" height="18" viewBox="0 0 14 18"><path d="M3 2l8 7-8 7" stroke="#fff" stroke-width="3" fill="none"/></svg></div>

<div class="abs ci" style="left:124px"><svg width="16" height="20" viewBox="0 0 9 11"><path d="M4.5 0a4 4 0 0 0-4 4c0 3 4 7 4 7s4-4 4-7a4 4 0 0 0-4-4z" fill="#8e88a8"/><circle cx="4.5" cy="4" r="1.5" fill="#2e2848"/></svg></div>
<div class="abs ct" style="left:190px;top:2764px"><h4>Address</h4><p>48 Linden Row</p></div>
<div class="abs ci on" style="left:364px"><svg width="24" height="18" viewBox="0 0 24 18" fill="none" stroke="#fff" stroke-width="2"><rect x="1" y="1" width="22" height="16" rx="2"/><path d="M1 2l11 8 11-8"/></svg></div>
<div class="abs ct" style="left:429px;top:2764px"><h4>Email Us</h4><p>hello@wellpathledgers.example</p></div>
<div class="abs ci" style="left:631px"><svg width="20" height="20" viewBox="0 0 20 20"><path d="M4 1l4 4-2 3c1 3 3 5 6 6l3-2 4 4-3 3C8 19 1 12 1 4z" fill="#8e88a8"/></svg></div>
<div class="abs ct" style="left:696px;top:2764px"><h4>Contact Us</h4><p>+044(2918) 530 61</p></div>
<div class="abs ci" style="left:858px"><svg width="22" height="22" viewBox="0 0 22 22" fill="none" stroke="#8e88a8" stroke-width="2"><circle cx="11" cy="11" r="9"/><path d="M11 6v5h4"/></svg></div>
<div class="abs ct" style="left:923px;top:2764px"><h4>Opening Hour</h4><p>Mon - Friday 10 am - 8pm</p></div>

<div class="abs foot-rule"></div>
<div class="abs copyright">WELLPATH LEDGERS</div>

</body>
</html>
```